Landing Page and Logo for Auto-Blogging Platform

I created a platform that allows users to start a blog for their business, hobby, charity, etc. I need a landing page where users can learn about the platform, benefits of consistent blogging, SEO value, plans/pricing, etc. The landing page needs to have multiple call to action buttons encouraging the visitor to register/sign up for a free trial.

In addition to the landing page, I need a page for users to establish the settings for their blog. This page should be a fairly simple form, intended for the user to enter a few details to set up their blog:
1. Name of Blog
2. Up to 10 topics and/or keywords the blog should focus on
3. Theme: Color-scheme and logo upload for blog.

I have attached the specifications of the platform's functionality so you can better understand how it works, plans/pricing, etc.

I also need a logo for the business. The name of the platform is PostNook.

Target Market(s)

Website owners, bloggers, business owners

Industry/Entity Type

Technology, Internet, web design

Coding

Coded - Design and coding required

Number of Pages Required

2 page

Colors
0054AA
0677BA
7BADD7
CADEEF
E8F1F8
0094D4
00A9DD
6FCCEA
C7EBF8
E9F6FB

Requirements
Must have
• Eye-catching design but fairly light on content (keep it simple and brief.)
Nice to have
• Eye-catching yet simple design, clean and easy to understand what we are offering.
Should not have
• Too much “wordy” and confusing content.

```html
<!DOCTYPE html>
<html lang="en">
<head>
<meta charset="utf-8">
<title>PostNook — Your Blog Is a Reflection of You</title>
<link href="https://fonts.googleapis.com/css2?family=Poppins:wght@400;500;600;700;800&display=swap" rel="stylesheet">
<style>
:root{
  --blue-deep:#0054AA;
  --blue-mid:#0677BA;
  --blue-soft:#7BADD7;
  --blue-pale:#CADEEF;
  --blue-mist:#E8F1F8;
  --cyan:#0094D4;
  --cyan-bright:#00A9DD;
  --cyan-soft:#6FCCEA;
  --ink:#111111;
  --text:#555a63;
  --white:#ffffff;
  --footer:#0d0d0f;
}
*{margin:0;padding:0;box-sizing:border-box}
html,body{width:1200px;height:3560px;overflow:hidden}
body{font-family:'Poppins',sans-serif;color:var(--ink);background:var(--white);position:relative}
.abs{position:absolute}
.btn{position:absolute;display:flex;align-items:center;justify-content:center;border-radius:24px;color:var(--white);font-weight:600;font-size:16px;background:linear-gradient(90deg,var(--cyan-bright),var(--blue-deep));text-decoration:none}

/* header */
.topline{top:0;left:0;width:1200px;height:4px;background:var(--blue-deep)}
.header{top:4px;left:0;width:1200px;height:90px;background:var(--white)}
.brand{position:absolute;display:flex;align-items:center;gap:10px;font-weight:700;color:var(--blue-deep)}
.brand .dot{width:14px;height:14px;border-radius:50%;background:var(--cyan)}
.header .brand{left:110px;top:28px;font-size:29px}
.nav a{position:absolute;top:32px;font-size:16px;color:#555;text-decoration:none}
.nav a.active{color:var(--blue-deep);font-weight:600}
.nav .under{position:absolute;left:449px;top:60px;width:46px;height:3px;border-radius:2px;background:var(--blue-deep)}
.header .btn{left:954px;top:22px;width:133px;height:44px}

/* hero */
.hero{top:94px;left:0;width:1200px;height:503px;background:linear-gradient(90deg,#cfdcea 0%,#dde6ef 45%,#b9c9dc 100%)}
.hero-photo{position:absolute;left:560px;top:0;width:640px;height:503px;background:linear-gradient(120deg,#d9e2ec 0%,#7f97b2 40%,#3c4d62 75%,#c4ccd6 100%)}
.hero h1{position:absolute;left:73px;top:58px;font-size:62px;font-weight:800;color:var(--blue-deep);line-height:1}
.hero h2{position:absolute;left:73px;top:134px;font-size:44px;font-weight:800;color:var(--blue-deep);line-height:1}
.hero h3{position:absolute;left:73px;top:196px;width:560px;font-size:33px;font-weight:800;color:var(--ink);line-height:50px}
.hero p{position:absolute;left:73px;top:304px;width:520px;font-size:16px;line-height:31px;color:#222}
.hero .btn{left:73px;top:387px;width:151px;height:45px}
.scroll-bump{position:absolute;left:540px;top:554px;width:120px;height:50px}

/* methods */
.section-title{position:absolute;left:0;width:1200px;text-align:center;font-weight:700;text-transform:uppercase}
.methods-title{top:684px;font-size:33px}
.methods-title span{color:var(--cyan)}
.swoosh{position:absolute;left:540px;width:120px;height:20px}
.lead{position:absolute;left:170px;top:789px;width:860px;text-align:center;font-size:16px;line-height:34px;color:var(--text)}
.step-img{position:absolute;width:424px;height:284px;border-radius:22px}
.step-num{position:absolute;width:42px;height:42px;border-radius:50%;background:var(--cyan-bright);color:var(--white);font-weight:600;font-size:16px;display:flex;align-items:center;justify-content:center}
.step-text{position:absolute;width:380px}
.step-text h4{font-size:19px;font-weight:500;line-height:33px;color:var(--ink);margin-bottom:10px}
.step-text p{font-size:13.5px;line-height:28px;color:var(--text)}
.step-text.right{text-align:right}

/* pricing */
.pricing{top:1940px;left:0;width:1200px;height:615px;background:linear-gradient(180deg,#0a4fa8,#0550b0);}
.pricing .section-title{top:68px;font-size:33px;color:var(--white)}
.plan{position:absolute;top:179px;width:310px;height:362px;border:1px solid rgba(255,255,255,.25);border-radius:22px;background:rgba(10,70,160,.55);text-align:center;color:var(--white)}
.plan.featured{background:var(--white);color:var(--ink);border:none}
.plan h5{margin-top:26px;font-size:28px;font-weight:700;color:var(--white)}
.plan.featured h5{color:var(--blue-deep)}
.plan .band{margin-top:12px;height:60px;background:var(--white);color:var(--blue-deep);font-size:17px;font-weight:500;display:flex;align-items:center;justify-content:center}
.plan.featured .band{background:var(--blue-deep);color:var(--white)}
.plan .price{margin-top:18px;font-size:30px;font-weight:700;color:var(--white)}
.plan.featured .price{color:var(--blue-deep)}
.plan .price small{font-size:13px;font-weight:600}
.plan p{margin:10px auto 0;width:250px;font-size:13.5px;line-height:27px;color:#e6eefa}
.plan.featured p{color:var(--text)}
.plan .btn{left:88px;bottom:36px;width:135px;height:38px;font-size:15px}

/* about */
.about-circle{left:112px;top:2687px;width:445px;height:445px;border-radius:50%;background:linear-gradient(160deg,var(--cyan-bright),var(--blue-deep))}
.about-screen{left:88px;top:2750px;width:495px;height:321px;border-radius:14px;background:linear-gradient(180deg,#2c2f36,#8d939c 85%,#d9dbdf)}
.about h2{position:absolute;left:650px;top:2676px;font-size:33px;font-weight:700}
.about h2 span{color:var(--cyan)}
.about p{position:absolute;left:636px;width:475px;font-size:16px;line-height:33.5px;color:var(--text)}
.about .btn{left:636px;top:3090px;width:146px;height:43px}

/* footer */
.footer{top:3256px;left:0;width:1200px;height:304px;background:var(--footer)}
.footer .brand{left:0;width:1200px;justify-content:center;top:66px;font-size:44px;color:var(--cyan)}
.footer-nav{position:absolute;top:154px;left:0;width:1200px;display:flex;justify-content:center;gap:68px}
.footer-nav a{color:var(--white);font-size:16px;text-decoration:none}
.socials{position:absolute;top:202px;left:0;width:1200px;display:flex;justify-content:center;gap:10px}
.socials span{width:40px;height:40px;border-radius:50%;background:var(--blue-deep);display:block}
.copyright{position:absolute;top:260px;left:0;width:1200px;text-align:center;color:var(--white);font-size:12px}
</style>
</head>
<body>

<div class="abs topline"></div>
<header class="abs header">
  <div class="brand"><span class="dot"></span>POSTNOOK</div>
  <nav class="nav">
    <a class="active" style="left:449px">Home</a>
    <span class="under"></span>
    <a style="left:541px">About Us</a>
    <a style="left:654px">Services</a>
    <a style="left:763px">Reviews</a>
    <a style="left:870px">Blogs</a>
  </nav>
  <a class="btn">Contact Us</a>
</header>

<section class="abs hero">
  <div class="hero-photo" role="img" aria-label="Man working at a desktop computer with a laptop nearby"></div>
  <h1>YOUR BLOG IS A</h1>
  <h2>REFLECTION OF YOU.</h2>
  <h3>MAKE SURE IT REFLECTS YOUR BEST SELF.</h3>
  <p>At vero eos et accusamus et iusto odio dignissimos ducimus qui blanditiis praesentium voluptatum deleniti atq</p>
  <a class="btn">Get Started</a>
</section>
<svg class="scroll-bump" viewBox="0 0 120 50">
  <path d="M0 43 C30 43 35 0 60 0 C85 0 90 43 120 43 L120 50 L0 50Z" fill="#fff"/>
  <rect x="50" y="8" width="20" height="30" rx="10" fill="#888"/>
  <path d="M60 14 V30 M54 25 L60 31 L66 25" stroke="#fff" stroke-width="2" fill="none"/>
</svg>

<h2 class="section-title methods-title">Methods to create <span>blog topics</span></h2>
<svg class="swoosh" style="top:746px" viewBox="0 0 120 20"><path d="M2 16 Q60 -4 118 4 Q60 4 2 16Z" fill="#111"/></svg>
<p class="lead">Denounce with righteous indignation and dislike men who are so beguiled and demoralized by the charms of pleasure of the moment, so blinded by desire, that they cannot foresee the pain and trouble</p>

<svg class="abs" style="left:0;top:0" width="1200" height="1800">
  <path d="M645 1078 V1195 Q645 1209 631 1209 H575 Q561 1209 561 1223 V1346 M561 1388 V1512 Q561 1526 575 1526 H631 Q645 1526 645 1540 V1671" fill="none" stroke="#0054AA" stroke-width="2" stroke-dasharray="2 4"/>
</svg>

<div class="step-img" style="left:180px;top:902px;background:linear-gradient(135deg,#f1f3f6,#b9c6d6 60%,#4a5c74)" role="img" aria-label="Hand touching a tablet with floating images"></div>
<div class="step-num" style="left:624px;top:1036px">01</div>
<div class="step-text" style="left:695px;top:964px">
  <h4>The user enters them into a table manually</h4>
  <p>Lorem ipsum dolor sit amet, consectetur adipiscing elit, sed do eiusmod tempor incididunt ut labore et dolore magna aliqua.</p>
</div>

<div class="step-text right" style="left:115px;top:1288px">
  <h4>The user uploads a list of blog topics in CSV format.</h4>
  <p>Lorem ipsum dolor sit amet, consectetur adipiscing elit, sed do eiusmod tempor incididunt ut labore et dolore magna aliqua. Ut enim ad</p>
</div>
<div class="step-num" style="left:540px;top:1346px">02</div>
<div class="step-img" style="left:596px;top:1235px;height:266px;background:radial-gradient(circle at 50% 55%,#f4f7ff 0%,#6f8fc4 22%,#1d2d55 60%,#6a4a32 100%)" role="img" aria-label="Hands above a glowing grid of media tiles"></div>

<div class="step-img" style="left:180px;top:1551px;background:radial-gradient(circle at 45% 40%,#bfe0ff 0%,#2f74d0 35%,#0a2f7a 80%)" role="img" aria-label="Robotic hand holding a glowing digital globe"></div>
<div class="step-num" style="left:624px;top:1671px">03</div>
<div class="step-text" style="left:695px;top:1613px">
  <h4>AI can create the list of blog topics based on a prompt</h4>
  <p>“Provide a list of 52 blog topics for a handyman business’s blog</p>
</div>

<section class="abs pricing">
  <h2 class="section-title">Our subscriptions plan</h2>
  <svg class="swoosh" style="top:128px" viewBox="0 0 120 20"><path d="M2 16 Q60 -4 118 4 Q60 4 2 16Z" fill="#fff"/></svg>
  <div class="plan" style="left:111px">
    <h5>BASE PLAN</h5>
    <div class="band">1 Blog Post (up to 2,000 words)</div>
    <div class="price">$9.99<small>/mo. Every Month</small></div>
    <p>Exercitation ullamco laboris nisi ut ali quip ex ea commodo cons</p>
    <a class="btn">Choose Plan</a>
  </div>
  <div class="plan featured" style="left:445px">
    <h5>PREMIUM PLAN</h5>
    <div class="band">1 Blog Post (up to 2,000 words)</div>
    <div class="price">$14.99<small>/mo. Every Week</small></div>
    <p>Exercitation ullamco laboris nisi ut ali quip ex ea commodo cons</p>
    <a class="btn">Choose Plan</a>
  </div>
  <div class="plan" style="left:779px">
    <h5>ULTIMATE PLAN</h5>
    <div class="band">1 Blog Post (up to 3,000 words)</div>
    <div class="price">$24.99<small>/mo. Every Day</small></div>
    <p>Exercitation ullamco laboris nisi ut ali quip ex ea commodo cons</p>
    <a class="btn">Choose Plan</a>
  </div>
</section>

<section class="about">
  <div class="abs about-circle"></div>
  <div class="abs about-screen" role="img" aria-label="Laptop showing the blog dashboard with charts"></div>
  <h2>ABOUT <span>US</span></h2>
  <svg class="swoosh" style="left:650px;top:2728px" viewBox="0 0 120 20"><path d="M2 16 Q60 -4 118 4 Q60 4 2 16Z" fill="#111"/></svg>
  <p style="top:2780px">The purpose of this platform is to allow anyone to start a blog and automate the process of creating content and posting it to the blog.</p>
  <p style="top:2895px">Each user will have a dashboard where they control their settings such as account information, billing, view blog posts, view blog post topics, etc. From this dashboard, the user can customize the “look and feel” of their blog including theme, hero banner, header, footer, logo, color scheme, etc.</p>
  <a class="btn">Read More</a>
</section>

<footer class="abs footer">
  <div class="brand"><span class="dot"></span>POSTNOOK</div>
  <nav class="footer-nav"><a>Home</a><a>About Us</a><a>Services</a><a>Reviews</a><a>Blogs</a><a>Contact Us</a></nav>
  <div class="socials"><span></span><span></span><span></span><span></span><span></span></div>
  <p class="copyright">(C) Copyright 2024 | All Rights Reserved</p>
</footer>

</body>
</html>
```